Single-sided business card for restaurant velmora with new logo made on this site

Business card options with new logo including restaurant name, address, phone number and website. This business card is single-sided only and will be presented at the hostess desk for clients to take. I would like to see options based on a cream card background, a white card background, a yellow card background and a burgundy colored background. It needs to be elegant and traditional.

Target Market(s)

local and international crowd

Industry/Entity Type

restaurant

Contact Information for Business Card

address, website and phone number

Font styles to use
Serif

Colors
EE7325
F08F49
F5BC92
FAE3D3
FDF4ED

Requirements
Must have
• new logo, address, phone number, website
Should not have
• more than three colors

```html
<!DOCTYPE html>
<html lang="es">
<head>
<meta charset="utf-8">
<title>Restaurant Velmora – Tarjeta de presentación</title>
<link rel="stylesheet" href="https://fonts.googleapis.com/css2?family=Tinos:wght@400;700&display=swap">
<style>
  :root {
    --backdrop: #e4e4e4;
    --card-cream: #fdeed3;
    --card-cream-deep: #fbe3b9;
    --ink: #3b1a14;
    --band: #3a0d0e;
    --mark-gold: #f2b33d;
  }
  * { box-sizing: border-box; margin: 0; padding: 0; }
  html, body {
    width: 1200px;
    height: 940px;
    overflow: hidden;
    background: var(--backdrop);
  }
  .business-card {
    position: absolute;
    left: 60px;
    top: 162px;
    width: 1080px;
    height: 616px;
    border-radius: 30px;
    overflow: hidden;
    background: var(--card-cream);
    font-family: "Tinos", "Times New Roman", serif;
    color: var(--ink);
  }
  .leaf-decoration {
    position: absolute;
    right: 0;
    top: 20px;
    width: 620px;
    height: 580px;
    background: radial-gradient(ellipse at 70% 75%, var(--card-cream-deep) 0%, rgba(251, 227, 185, 0.5) 45%, rgba(253, 238, 211, 0) 75%);
  }
  .bottom-band {
    position: absolute;
    left: 0;
    bottom: 0;
    width: 100%;
    height: 19px;
    background: var(--band);
  }
  .brand {
    position: absolute;
    left: 212px;
    top: 175px;
    width: 266px;
    display: flex;
    flex-direction: column;
    align-items: center;
  }
  .brand-square {
    width: 146px;
    height: 146px;
    background: var(--mark-gold);
  }
  .brand-name {
    margin-top: 22px;
    font-size: 46px;
    font-weight: 400;
    letter-spacing: 10px;
    padding-left: 10px;
    line-height: 1;
    color: var(--ink);
  }
  .contact {
    position: absolute;
    left: 547px;
    top: 168px;
  }
  .contact-heading {
    font-size: 28px;
    font-weight: 700;
    line-height: 34px;
  }
  .contact-address {
    font-style: normal;
    font-size: 27px;
    line-height: 34px;
  }
  .reservations {
    margin-top: 12px;
  }
  .reservations-phone {
    font-size: 34px;
    line-height: 38px;
  }
  .contact-web {
    margin-top: 14px;
    font-size: 27px;
    font-weight: 700;
    letter-spacing: 0.5px;
  }
</style>
</head>
<body>
  <article class="business-card">
    <div class="leaf-decoration" role="img" aria-label="Faint agave leaf decoration in pale cream tones"></div>

    <div class="brand">
      <div class="brand-square"></div>
      <div class="brand-name">VELMORA</div>
    </div>

    <section class="contact">
      <h1 class="contact-heading">Restaurant Velmora</h1>
      <address class="contact-address">
        Calle Jacaranda 415<br>
        Bahías del Arenal<br>
        Costa Sur CP 40125
      </address>
      <div class="reservations">
        <h2 class="contact-heading">Reservaciones</h2>
        <p class="reservations-phone">555-014-2283</p>
      </div>
      <p class="contact-web">www.velmora.com.mx</p>
    </section>

    <div class="bottom-band"></div>
  </article>
</body>
</html>
```